Women's Jewellery startup needs a captivating, beautifully designed and intuitive online store

[12/24 update]

Added 2 additional documents:

Feedback on designs received so far: designer feedback.docx
Product images from catalogue: products images.docx

Please read the feedback provided on designs provided so far to guide you further on your submission. The product images can be used to create promotional banners for the site.

@@@Added a document (VELISTO JEWELLERY_checklist.docx) which can be used by designers as a checklist when submitting their designs to ensure all aspects of the requirements have been covered @@@

+++IMPORTANT BUT NOT SPECIFIED IN THE REQUIREMENTS DOCUMENT - DESIGN SHOULD INCLUDE SUPPORT FOR MOBILE FRIENDLY SITE TOO+++

***Previous experience designing Jewellery online stores preferred (not essential)***

The name of the online Jewellery store is "Velisto Jewellery" and the business is based in Hong Kong. It will be run by 2 stay at home mothers. We need a Shopify themed store designed that will achieve the following objectives in order of priority:

• Conversion: The primary objective of the design/content is to prompt the customer to make a purchase. While this may sound obvious, it is mentioned so as not to distract the design process by focusing on other objectives (which are also important). The site also needs to be optimized so as to rank high in search engine searches for relevant keywords (SEO)
• Navigation: An intuitive interface which takes away a lot of the thinking from the customer by making it obvious what they need to do when they visit the store
• Engagement: Encourages the customer to spend time on the website and share content with their social network

Where applicable, the design of the store should reflect as closely as possible the mission statements and words outlined below:

• Jewellery you’ll fall in love with
• We want every client to leave the store with a smile
• We want to be able to provide the best service we can in every situation no matter what
• We aim to increase our business by word of mouth; therefore we tell people things about our store that makes it interesting for them to share
• We love every customer, no matter how difficult things get
• We, as a team, are so well informed about our products and brands that we always have the best information for our customers
• We celebrate women here!
• We celebrate life in here!
• We celebrate beauty here!
• We celebrate families here, as jewellery often stays within families.
• We will always try to make an extra step
• We will always try to exceed the expectation of our customers
• We will go as far as we possibly can to attract a customer back to our store and connect with us
• Every client that leaves our store knows more about jewellery because we passionately told him about it
• Romantic, classic, love, warm, cool, stylish

A draft functional specification is attached with this brief. We would like the design to reflect as closely as possible the functional requirements outlined in the document. Open to suggestions to improve upon the functional requirements.

Target Market(s)

Women aged 18-55

Industry/Entity Type

Jewelry Store

Coding

Coded - Design and coding required

Number of Pages Required

5+ page

Font styles to use
Other font styles liked:
• Myriad Pro as per Logo but open to any font that complements this one

Requirements
Must have
• 1. A look that encourages the user to make a purchase
• 2. An intuitive, easy to navigate and engaging interface
• 3. Primary colour scheme as defined in the functional specification attached
• 4. Simplistic look, not too cluttered
Nice to have
• 1. Closely matching the functional requirements of the site as outlined in the requirements specification but open to any better ideas

```html
<!DOCTYPE html>
<html lang="en">
<head>
<meta charset="utf-8">
<title>Velisto Jewellery</title>
<link href="https://fonts.googleapis.com/css2?family=Open+Sans:ital,wght@0,400;0,600;0,700;0,800;1,700&family=Source+Sans+3:wght@400;600;700&display=swap" rel="stylesheet">
<style>
:root{
  --gold:#c9a04f;
  --gold-dark:#b58a3a;
  --ink:#1d1d1d;
  --text:#555;
  --muted:#8a8a8a;
  --tile:#efefef;
  --line:#e4e4e4;
  --footer:#1e1e1e;
  --white:#fff;
  --star:#e1a33a;
}
*{margin:0;padding:0;box-sizing:border-box}
html,body{width:1200px;height:2609px;overflow:hidden;background:var(--white)}
body{position:relative;font-family:"Source Sans 3",Arial,sans-serif;color:var(--text)}
.abs{position:absolute}
/* header */
.site-header{position:absolute;left:0;top:0;width:1200px;height:123px;background:var(--white)}
.brand{position:absolute;left:249px;top:40px;display:flex;align-items:center;gap:10px}
.brand-mark{width:16px;height:16px;background:var(--gold)}
.brand-name{font-family:"Open Sans",sans-serif;font-weight:600;font-size:22px;letter-spacing:4px;color:var(--gold)}
.main-nav{position:absolute;top:52px;left:482px;font-size:13px;color:#444}
.main-nav a{position:absolute;white-space:nowrap;text-decoration:none;color:inherit}
.header-icons{position:absolute;top:49px;left:868px}
/* hero */
.hero{position:absolute;left:0;top:123px;width:1200px;height:506px;background:#050505}
.hero-photo{position:absolute;right:0;top:0;width:704px;height:506px;background:radial-gradient(ellipse at 55% 45%,#c69b84 0%,#6b4a38 35%,#2a1d17 65%,#050505 90%)}
.hero-tag{position:absolute;left:249px;top:152px;width:160px;height:38px;background:var(--gold);color:var(--white);font-family:"Open Sans",sans-serif;font-weight:700;font-size:23px;line-height:38px;text-align:center;letter-spacing:.5px}
.hero-title{position:absolute;left:247px;top:193px;font-family:"Open Sans",sans-serif;font-weight:800;font-size:51px;color:var(--white);letter-spacing:-.5px;line-height:60px}
.hero-sub{position:absolute;left:249px;top:252px;font-family:"Open Sans",sans-serif;font-size:28px;color:var(--white);line-height:34px}
.btn-outline{position:absolute;border:1px solid var(--white);color:var(--white);font-size:11px;font-weight:700;text-align:center}
.hero .btn-outline{left:249px;top:300px;width:120px;height:38px;line-height:36px}
/* sections */
.heading-small{position:absolute;left:0;width:1200px;text-align:center;font-family:"Open Sans",sans-serif;font-weight:800;font-size:16px;color:var(--ink)}
.heading-gold{position:absolute;left:0;width:1200px;text-align:center;font-family:"Open Sans",sans-serif;font-weight:800;font-size:28px;color:var(--gold)}
.dots{position:absolute;left:591px;width:20px;height:12px}
.lead{position:absolute;left:320px;width:560px;text-align:center;font-size:11px;line-height:18px;color:var(--muted)}
.decor{position:absolute}
.cat-tile{position:absolute;background:var(--tile)}
.cat-art{position:absolute;left:15%;top:12%;width:70%;height:50%;border-radius:50%;background:radial-gradient(ellipse,#e0c98d 0%,#cfcfcf 60%,var(--tile) 100%)}
.cat-label{position:absolute;bottom:16px;left:33px;width:94px;height:32px;background:var(--white);font-size:10px;font-weight:700;color:var(--ink);line-height:32px;padding-left:18px}
.cat-label::after{content:"";position:absolute;right:0;top:0;border-top:32px solid var(--gold);border-left:22px solid transparent}
.cat-feature{position:absolute;left:426px;top:831px;width:346px;height:331px;background:radial-gradient(ellipse at 50% 40%,#c28f72 0%,#7d5548 40%,#3a2b2c 85%)}
/* featured */
.tab{position:absolute;top:1313px;height:23px;line-height:23px;width:66px;text-align:center;font-size:9px;background:var(--tile);color:#555}
.tab.is-active{background:var(--gold);color:var(--white);font-weight:700}
.product{position:absolute;top:1365px;width:163px}
.product-photo{height:217px;background:var(--tile);position:relative}
.product-art{position:absolute;left:30px;top:50px;width:103px;height:110px;border-radius:50%;background:radial-gradient(ellipse,#e7d29a 0%,#d6d6d6 55%,var(--tile) 100%)}
.badge{position:absolute;left:8px;top:10px;width:30px;height:30px;border-radius:50%;background:var(--gold);color:var(--white);font-size:9px;font-weight:700;text-align:center;line-height:30px}
.product-row{display:flex;justify-content:space-between;margin-top:10px;font-size:11px;font-weight:700;color:var(--ink)}
.stars{color:var(--star);font-size:8px;letter-spacing:-.5px}
.product-desc{font-size:9px;line-height:13px;color:var(--muted);margin-top:6px}
.price{font-size:11px;font-weight:700;color:var(--ink);margin-top:6px}
.arrow{position:absolute;top:1460px;width:36px;height:36px;border-radius:50%;background:#2b2b2b}
/* banners */
.banner{position:absolute;top:1722px;height:318px;width:579px}
.banner-left{left:0;background:linear-gradient(90deg,#3a2a33 0%,#6a3f6e 45%,#5b3f86 100%)}
.banner-right{left:621px;background:linear-gradient(90deg,#2a1d18 0%,#3b2a22 50%,#231a17 100%)}
.frame{position:absolute;left:310px;top:56px;width:224px;height:208px;border:5px solid var(--white)}
.promo-script{position:absolute;left:0;width:100%;text-align:center;font-family:"Open Sans",sans-serif;font-style:italic;font-weight:700;color:var(--white)}
.promo-box{position:absolute;left:22px;top:60px;width:180px;height:42px;background:var(--gold);color:var(--white);font-family:"Open Sans",sans-serif;font-style:italic;font-weight:700;font-size:30px;line-height:42px;text-align:center}
.promo-note{position:absolute;left:0;top:114px;width:100%;text-align:center;font-size:10px;color:var(--white)}
.banner-left .btn-outline{left:52px;top:136px;width:98px;height:26px;line-height:24px;font-size:10px}
/* features */
.features{position:absolute;left:0;top:2099px;width:1200px;height:162px;background:#f6f6f6}
.feature{position:absolute;top:0;width:404px;height:162px;text-align:center}
.feature.is-center{background:#f3f3f3;border:1px solid var(--line)}
.feature svg{position:absolute;left:182px;top:38px}
.feature h3{position:absolute;left:0;top:95px;width:100%;font-family:"Open Sans",sans-serif;font-weight:700;font-size:13px;color:var(--ink)}
.feature p{position:absolute;left:0;top:113px;width:100%;font-size:11px;color:#333}
/* footer */
.site-footer{position:absolute;left:0;top:2320px;width:1200px;height:254px;background:var(--footer);color:#b7b7b7}
.footer-col{position:absolute;top:42px}
.footer-col h4{font-family:"Open Sans",sans-serif;font-weight:700;font-size:14px;color:var(--white);margin-bottom:16px}
.footer-col p{font-size:9.5px;line-height:16.5px}
.footer-col li{list-style:none;font-size:9.5px;line-height:24px}
.footer-col li::before{content:"»";margin-right:8px;color:#888}
.socials{display:flex;gap:7px;margin-top:12px}
.socials span{width:22px;height:22px;border-radius:50%;background:var(--gold)}
.newsletter{display:flex;margin-top:18px;width:164px;height:30px}
.newsletter span{flex:1;background:#2c2c2c;font-size:9px;color:#777;line-height:30px;padding-left:10px}
.newsletter b{width:34px;background:var(--gold);position:relative}
.legal{position:absolute;left:0;top:2574px;width:1200px;height:35px;background:var(--gold);color:var(--white);font-size:9px;line-height:35px;padding-left:249px}
</style>
</head>
<body>

<header class="site-header">
  <div class="brand"><span class="brand-mark"></span><span class="brand-name">VELISTO</span></div>
  <nav class="main-nav">
    <a style="left:0">Home</a><a style="left:55px">Collections</a><a style="left:135px">Product</a><a style="left:198px">Blog</a><a style="left:245px">Contact us</a>
  </nav>
  <svg class="header-icons" width="86" height="24" viewBox="0 0 86 24" aria-label="Search, cart and menu">
    <g fill="none" stroke="#c9a04f" stroke-width="1.4">
      <circle cx="8" cy="10" r="6"/><line x1="12.5" y1="14.5" x2="17" y2="19"/>
      <path d="M31 8h12l-1.5 10h-9z"/><path d="M34 8a3 3 0 0 1 6 0"/>
      <rect x="67" y="4" width="18" height="14"/><line x1="71" y1="9" x2="81" y2="9"/><line x1="71" y1="13" x2="81" y2="13"/>
    </g>
    <circle cx="44" cy="18" r="3.5" fill="#c9a04f"/>
  </svg>
</header>

<section class="hero">
  <div class="hero-photo" role="img" aria-label="Smiling woman with flowing dark hair wearing a diamond necklace, earrings and ring"></div>
  <div class="hero-tag">JEWELLERY</div>
  <h1 class="hero-title">YOU’LL FALL</h1>
  <div class="hero-sub">IN LOVE WITH</div>
  <div class="btn-outline">Shop Now!</div>
</section>

<div class="decor" style="left:0;top:630px;width:122px;height:361px;background:radial-gradient(ellipse at 0% 70%,#f1d35a 0%,#d8ad2b 35%,rgba(216,173,43,0) 60%)" role="img" aria-label="Gold heart pendant on a chain"></div>

<h2 class="heading-small" style="top:674px">WELCOME TO</h2>
<h2 class="heading-gold" style="top:692px">VELISTO JEWELLERY</h2>
<svg class="dots" style="top:737px" viewBox="0 0 20 12"><circle cx="6" cy="6" r="5" fill="#c9a04f"/><circle cx="14" cy="6" r="5" fill="none" stroke="#ddd"/></svg>
<p class="lead" style="top:759px">Lorem Ipsum is simply dummy text of the printing and typesetting industry. Lorem Ipsum has been the industry's standard dummy text ever since the 1500s, when an unknown printer took a galley of type and scrambled it to make a type specimen book</p>

<div class="cat-tile" style="left:249px;top:831px;width:165px;height:122px"><div class="cat-art" role="img" aria-label="Gold bangle bracelet"></div><div class="cat-label">BRACELETS</div></div>
<div class="cat-tile" style="left:249px;top:967px;width:165px;height:195px"><div class="cat-art" role="img" aria-label="Diamond stud earrings"></div><div class="cat-label">EARRINGS</div></div>
<div class="cat-feature" role="img" aria-label="Woman wearing a gold necklace and ring"><div class="cat-label" style="left:14px;bottom:14px">RINGS</div></div>
<div class="cat-tile" style="left:786px;top:831px;width:165px;height:195px"><div class="cat-art" role="img" aria-label="Ruby and gold statement necklace"></div><div class="cat-label">NECKLACES</div></div>
<div class="cat-tile" style="left:786px;top:1040px;width:165px;height:122px"><div class="cat-art" role="img" aria-label="Charm bracelet"></div><div class="cat-label">CHARMS</div></div>

<h2 class="heading-gold" style="top:1210px">FEATURED PRODUCTS</h2>
<p class="lead" style="top:1250px;font-size:11px;color:#666">Lorem Ipsum is simply dummy text of the printing and typesetting industry</p>
<svg class="dots" style="top:1283px" viewBox="0 0 20 12"><circle cx="6" cy="6" r="5" fill="none" stroke="#ddd"/><circle cx="14" cy="6" r="5" fill="#c9a04f"/></svg>

<div class="tab is-active" style="left:417px">Rings</div>
<div class="tab" style="left:492px">Bracelets</div>
<div class="tab" style="left:567px">Necklaces</div>
<div class="tab" style="left:642px">Charms</div>
<div class="tab" style="left:716px">Earrings</div>

<article class="product" style="left:249px"><div class="product-photo"><div class="product-art" role="img" aria-label="Diamond solitaire ring"></div><span class="badge">-20</span></div><div class="product-row"><span>Rings</span><span class="stars">★★★★★</span></div><p class="product-desc">Lorem Ipsum is simply dummy text of the printing and typesetting industry</p><p class="price">$125.00</p></article>
<article class="product" style="left:430px"><div class="product-photo"><div class="product-art" role="img" aria-label="Gold bangle"></div></div><div class="product-row"><span>Bracelets</span><span class="stars">★★★★★</span></div><p class="product-desc">Lorem Ipsum is simply dummy text of the printing and typesetting industry</p><p class="price">$231.00</p></article>
<article class="product" style="left:609px"><div class="product-photo"><div class="product-art" role="img" aria-label="Gold fringe necklace"></div><span class="badge">-45</span></div><div class="product-row"><span>Necklaces</span><span class="stars">★★★★★</span></div><p class="product-desc">Lorem Ipsum is simply dummy text of the printing and typesetting industry</p><p class="price">$145.00</p></article>
<article class="product" style="left:790px"><div class="product-photo"><div class="product-art" role="img" aria-label="Diamond earrings"></div></div><div class="product-row"><span>Earrings</span><span class="stars">★★★★★</span></div><p class="product-desc">Lorem Ipsum is simply dummy text of the printing and typesetting industry</p><p class="price">$251.00</p></article>

<svg class="arrow" style="left:220px" viewBox="0 0 36 36" aria-label="Previous"><path d="M20 12l-6 6 6 6" fill="none" stroke="#fff" stroke-width="2"/></svg>
<svg class="arrow" style="left:945px" viewBox="0 0 36 36" aria-label="Next"><path d="M16 12l6 6-6 6" fill="none" stroke="#fff" stroke-width="2"/></svg>

<div class="decor" style="left:1000px;top:1522px;width:200px;height:200px;background:radial-gradient(ellipse at 70% 50%,#e9b73a 0%,#c98f1e 40%,rgba(201,143,30,0) 70%)" role="img" aria-label="Pair of gold wedding rings"></div>

<section class="banner banner-left" role="img" aria-label="Woman with dark curls and purple lipstick wearing a cocktail ring, with a blue brush stroke">
  <div class="frame">
    <div class="promo-script" style="top:14px;font-size:24px">Velisto</div>
    <div class="promo-box">Jewellery</div>
    <div class="promo-note">50% off on Rings and Earrings Diamond</div>
    <div class="btn-outline">Shop Now!</div>
  </div>
</section>

<section class="banner banner-right" role="img" aria-label="Woman in black lace with a drop earring, shown in profile">
  <svg style="position:absolute;left:20px;top:76px" width="240" height="170" viewBox="0 0 240 170">
    <path d="M20 40 Q120 -10 220 40 L232 85 L220 130 Q120 180 20 130 L8 85 Z" fill="#fff"/>
    <path d="M30 48 Q120 4 210 48 L220 85 L210 122 Q120 166 30 122 L20 85 Z" fill="none" stroke="#c9a04f" stroke-width="1.5"/>
    <text x="120" y="62" text-anchor="middle" font-family="Open Sans,sans-serif" font-weight="700" font-size="13" fill="#c9a04f">VELISTO</text>
    <text x="120" y="90" text-anchor="middle" font-family="Open Sans,sans-serif" font-weight="800" font-size="24" fill="#c9a04f">JEWELLERY</text>
    <rect x="30" y="97" width="180" height="18" fill="#c9a04f"/>
    <text x="120" y="110" text-anchor="middle" font-family="Source Sans 3,sans-serif" font-size="9.5" fill="#fff">25% off on Rings and Earrings Diamond</text>
    <text x="120" y="135" text-anchor="middle" font-family="Source Sans 3,sans-serif" font-weight="700" font-size="10" fill="#c9a04f" text-decoration="underline">Shop Now!</text>
  </svg>
</section>

<section class="features">
  <div class="feature" style="left:0">
    <svg width="40" height="44" viewBox="0 0 40 44" fill="none" stroke="#c9a04f" stroke-width="1.6"><path d="M30 4c-10 2-18 12-20 22l8 8c10-2 20-10 22-20z"/><circle cx="26" cy="16" r="3"/><path d="M10 26l-6 2 4 6M18 34l-2 6-6-4M8 36l-4 6"/></svg>
    <h3>FREE SHIPPING &amp; RETURN</h3><p>Free shipping on orders over $49</p>
  </div>
  <div class="feature is-center" style="left:396px">
    <svg width="40" height="44" viewBox="0 0 40 44" fill="none" stroke="#c9a04f" stroke-width="1.6"><path d="M14 4h12l-4 8h-4z"/><path d="M16 12C4 18 4 40 20 40s16-22 4-28"/><path d="M24 22c-1-2-7-2-7 1s7 2 7 5-6 3-7 1M20 19v2M20 31v2"/></svg>
    <h3>MONEY GUARANTEE</h3><p>30 days money back guarantee</p>
  </div>
  <div class="feature" style="left:796px">
    <svg width="40" height="44" viewBox="0 0 40 44" fill="none" stroke="#c9a04f" stroke-width="1.6"><path d="M6 26v-6a14 14 0 0 1 28 0v6"/><rect x="4" y="24" width="7" height="12" rx="2"/><rect x="29" y="24" width="7" height="12" rx="2"/></svg>
    <h3>ONLINE SUPPORT</h3><p>We support online 24 hours a day</p>
  </div>
</section>

<footer class="site-footer">
  <div class="footer-col" style="left:249px;width:195px">
    <h4>About us</h4>
    <p>Lorem Ipsum is simply dummy text of the printing and typesetting industry. Lorem Ipsum has been the industry's standard dummy text ever since the 1500s, when an unknown printer took a galley of type and scrambled it to make a type specimen book</p>
    <div class="socials"><span></span><span></span><span></span><span></span></div>
  </div>
  <div class="footer-col" style="left:490px">
    <h4>Shopping</h4>
    <ul><li>My Wishlist</li><li>My Orders</li><li>Size Guide</li></ul>
  </div>
  <div class="footer-col" style="left:628px">
    <h4>Customer Care</h4>
    <ul><li>Delivery</li><li>Faqs</li><li>Returns</li><li>Care And Warranty</li><li>Contact us</li></ul>
  </div>
  <div class="footer-col" style="left:784px;width:170px">
    <h4>Newsletters</h4>
    <p>Lorem Ipsum is simply dummy text of the printing and typesetting industry.</p>
    <div class="newsletter"><span>Your Email Address</span><b><svg width="34" height="30" viewBox="0 0 34 30"><path d="M11 15l13-6-4 13-3-5z" fill="#fff"/></svg></b></div>
  </div>
</footer>

<div class="legal">Copyright © 2017 <b>Velisto Jewellery</b> All Rights</div>

</body>
</html>
```